New Dynamic Design Based on Other Site

We need a new website designed where the front page is VERY SEO Friendly. The front page should almost follow the same SEO principles that are on RankLoomPress.com. The inner pages need to follow the same exact video animations that occur on vollq.com. I'd like to keep our "marbletons" theme throughout the new design but we will provide all of the content but I want someone to design something SEO friendly, new blog theme, and actual inner pages that are dynamic and based on those short videos.

Check attached file for company name and site that we currently have. Feel free to pull the content from that site and re-use it and also leave placeholders for the rest of them.

PLEASE NO USE OF STOCK IMAGES. Use a designer or an illustrator to create the various images.

Please make sure the front page is SEO friendly! Make sure you familiarize yourself with the quorvix algorithm for SEO. Content above the fold H1 Tags Very mobile friendly Minimal javascript and animations Basically a quality static page with optimized content

Target Market(s)

call center companies, anything call related

Industry/Entity Type

Telecommunications

Number of Pages Required

4 page

Font styles to use
Sans Serif

Colors
33a6d7
85cae6
0792cd
0255a3
cee9f5
ecf7fb
ffffff

Requirements
Must have
• places for video animations
• dynamic functionality
• SEO friendly (front page)
Should not have
• should not look like a template. needs to be unique

```html
<!DOCTYPE html>
<html lang="en">
<head>
<meta charset="utf-8">
<title>VoxGrade — System Details</title>
<link href="https://fonts.googleapis.com/css2?family=Montserrat:wght@400;500;600;700&family=Open+Sans:wght@300;400&display=swap" rel="stylesheet">
<style>
:root{
  --sky:#33a6d7;
  --sky-soft:#85cae6;
  --azure:#0792cd;
  --navy:#0255a3;
  --ink:#0f2f52;
  --mist:#cee9f5;
  --haze:#ecf7fb;
  --white:#ffffff;
  --teal:#2f8fae;
  --coral:#e8663d;
  --sun:#f5c84c;
  --text:#4a4f55;
  --dark:#222;
}
*{margin:0;padding:0;box-sizing:border-box}
html,body{width:758px;height:1200px;overflow:hidden;background:var(--white)}
body{position:relative;font-family:"Open Sans",Arial,sans-serif;color:var(--text)}

/* header */
.site-header{position:absolute;left:0;top:0;width:758px;height:83px;background:var(--white)}
.brand{position:absolute;left:79px;top:52px;display:flex;align-items:center;gap:6px}
.brand-dot{width:16px;height:16px;border-radius:50%;background:var(--sky)}
.brand-name{font-family:"Montserrat",sans-serif;font-weight:600;font-size:18px;color:var(--ink);letter-spacing:-.3px}
.callout{position:absolute;left:461px;top:21px;display:flex;align-items:center;gap:8px}
.callout-icon{width:19px;height:19px;border-radius:50%;background:var(--azure);display:flex;align-items:center;justify-content:center}
.callout-label{font-family:"Montserrat",sans-serif;font-size:6.4px;color:var(--dark);font-weight:500}
.callout-number{font-family:"Montserrat",sans-serif;font-size:10.4px;font-weight:700;color:var(--azure);margin-top:1px}
.search{position:absolute;left:579px;top:17px;width:97px;height:22px;border:1px solid #cfd3d6;display:flex;align-items:center;padding-left:10px;gap:5px;font-family:"Montserrat",sans-serif;font-size:5.4px;color:#777}
.main-nav{position:absolute;top:61px;left:0;width:758px;height:10px;font-family:"Montserrat",sans-serif;font-size:6.3px;color:var(--dark);font-weight:500}
.main-nav span{position:absolute;top:0;white-space:nowrap}
.main-nav .current{color:var(--sky);font-weight:600}
.caret{display:inline-block;width:0;height:0;border-left:2.4px solid transparent;border-right:2.4px solid transparent;border-top:2.8px solid currentColor;margin-left:4px;vertical-align:middle}

/* hero */
.hero-art{position:absolute;left:0;top:83px;width:758px;height:280px;
  background:
    radial-gradient(ellipse 150px 95px at 300px 195px,rgba(31,120,165,.75),rgba(31,120,165,0) 100%),
    radial-gradient(ellipse 45px 110px at 595px 170px,rgba(60,165,195,.8),rgba(60,165,195,0) 100%),
    radial-gradient(ellipse 70px 40px at 700px 150px,rgba(30,60,85,.75),rgba(30,60,85,0) 100%),
    radial-gradient(ellipse 45px 35px at 520px 50px,rgba(232,102,61,.7),rgba(232,102,61,0) 100%),
    radial-gradient(circle 45px at 310px 55px,rgba(40,100,140,.55),rgba(40,100,140,0) 100%),
    linear-gradient(90deg,#d9edf6,#d0e8f3 55%,#d9edf6)}

/* content */
.feature-art{position:absolute;left:84px;top:410px;width:196px;height:204px;border-radius:50%;
  background:
    radial-gradient(circle 55px at 50% 48%,rgba(185,90,60,.55),rgba(185,90,60,0) 100%),
    radial-gradient(circle 45px at 28% 28%,rgba(232,102,61,.55),rgba(232,102,61,0) 100%),
    radial-gradient(circle 40px at 78% 25%,rgba(245,200,76,.7),rgba(245,200,76,0) 100%),
    radial-gradient(circle 40px at 25% 78%,rgba(245,200,76,.65),rgba(245,200,76,0) 100%),
    radial-gradient(circle 45px at 80% 75%,rgba(47,143,174,.55),rgba(47,143,174,0) 100%),
    radial-gradient(circle,#eaf4f9 0%,#f4f9fc 60%,var(--white) 72%)}
.section-title{position:absolute;left:327px;top:402px;font-family:"Montserrat",sans-serif;font-size:10.6px;font-weight:700;color:var(--ink);letter-spacing:.2px}
.title-rule{position:absolute;left:327px;top:422px;width:29px;height:1.5px;background:var(--sky)}
.copy{position:absolute;left:327px;width:332px;font-size:7.2px;line-height:12px;font-weight:400;color:var(--text)}
.bullets{position:absolute;left:330px;top:620px;list-style:none;font-size:7.2px;line-height:12px}
.bullets li{position:relative;padding-left:13px}
.bullets li::before{content:"";position:absolute;left:0;top:3px;border-top:2.5px solid transparent;border-bottom:2.5px solid transparent;border-left:3.5px solid var(--dark)}
.sub-title{position:absolute;left:330px;top:813px;font-family:"Montserrat",sans-serif;font-size:7.6px;font-weight:700;color:var(--ink)}
.benefits{position:absolute;left:331px;top:836px;list-style:none;font-size:7.2px;line-height:12px}
.benefits li span{display:inline-block;width:18px}

/* footer */
.site-footer{position:absolute;left:0;top:961px;width:758px;height:239px;background:var(--navy);color:var(--white)}
.f-head{position:absolute;top:37px;font-family:"Montserrat",sans-serif;font-size:6.8px;font-weight:700}
.f-list{position:absolute;top:57px;list-style:none;font-family:"Montserrat",sans-serif;font-size:5.4px;line-height:10px;font-variant:small-caps;letter-spacing:.2px}
.f-line{position:absolute;font-family:"Montserrat",sans-serif;font-size:5.4px;font-variant:small-caps}
.email-field{position:absolute;left:349px;top:61px;width:149px;height:24px;background:var(--white);color:#555;font-family:"Montserrat",sans-serif;font-size:5.6px;padding:9px 10px}
.signup{position:absolute;left:349px;top:93px;width:61px;height:20px;background:var(--sky);font-family:"Montserrat",sans-serif;font-size:7.6px;font-weight:700;text-align:center;line-height:20px;letter-spacing:.3px}
.f-brand{position:absolute;left:575px;top:71px;display:flex;align-items:center;gap:6px}
.f-brand .brand-dot{background:var(--white)}
.f-brand .brand-name{color:var(--white)}
.f-rule{position:absolute;left:84px;top:162px;width:591px;height:1px;background:rgba(255,255,255,.18)}
.follow{position:absolute;left:84px;top:197px;font-family:"Montserrat",sans-serif;font-size:6.8px;font-weight:700}
.social{position:absolute;top:192px;width:18px;height:18px;border-radius:50%}
.copyright{position:absolute;right:83px;top:198px;font-family:"Montserrat",sans-serif;font-size:5.8px;letter-spacing:.2px}
</style>
</head>
<body>

<header class="site-header">
  <div class="brand"><span class="brand-dot"></span><span class="brand-name">VoxGrade</span></div>
  <div class="callout">
    <span class="callout-icon">
      <svg width="9" height="9" viewBox="0 0 24 24"><path fill="#fff" d="M6.6 10.8a15 15 0 0 0 6.6 6.6l2.2-2.2a1 1 0 0 1 1-.25 11.4 11.4 0 0 0 3.6.57 1 1 0 0 1 1 1V20a1 1 0 0 1-1 1A17 17 0 0 1 3 4a1 1 0 0 1 1-1h3.5a1 1 0 0 1 1 1c0 1.25.2 2.45.57 3.57a1 1 0 0 1-.25 1z"/></svg>
    </span>
    <div>
      <div class="callout-label">CALL US NOW</div>
      <div class="callout-number">800.555.0142</div>
    </div>
  </div>
  <div class="search">
    <svg width="6" height="6" viewBox="0 0 12 12"><circle cx="5" cy="5" r="3.5" fill="none" stroke="#333" stroke-width="1.5"/><path d="M7.6 7.6 11 11" stroke="#333" stroke-width="1.5"/></svg>
    SEARCH
  </div>
  <nav class="main-nav">
    <span style="left:254px">HOME</span>
    <span style="left:293px">SERVICES<i class="caret"></i></span>
    <span class="current" style="left:352px">SYSTEM DETAILS<i class="caret"></i></span>
    <span style="left:432px">SAMPLE SCORECARDS</span>
    <span style="left:521px">PRICING</span>
    <span style="left:567px">TEAM</span>
    <span style="left:606px">BLOG</span>
    <span style="left:642px">CONTACT</span>
  </nav>
</header>

<div class="hero-art" role="img" aria-label="Illustration of a rotary telephone with a hand lifting the receiver, a clock, gears and a chat bubble on a pale blue background"></div>

<main>
  <div class="feature-art" role="img" aria-label="Illustration of a call center agent with headset at a laptop, surrounded by round icons for search, chat, time, mobile and ratings"></div>

  <h1 class="section-title">SYSTEM DETAILS</h1>
  <div class="title-rule"></div>

  <p class="copy" style="top:444px">VoxGrade provides comprehensive 3rd party quality assurance services combining state of the art voice-to-text technology with human analysts to evaluate agent performance for customer / agent interactions in order to maximize compliance and script adherence.</p>

  <p class="copy" style="top:499px">VoxGrade provides comprehensive 3rd party quality assurance (QA) services. With the use of human quality analysts combined with state of the art voice-to-text technology, VoxGrade evaluates and scores agent-customer interactions to identify key behaviors and procedures that drive sales, create satisfied customers, and keep organizations compliant.</p>

  <p class="copy" style="top:564px">Organizations that have outsourced their QA program to VoxGrade have on average benefited from month over month reductions in compliance violations at a rate of 7%, while improving lead conversion and customer retention at a rate of 12% and 9% respectively.</p>

  <ul class="bullets">
    <li>Starting at only 15¢ per CALL minute with NO setup fees or ongoing maintenance</li>
    <li>Integrated voice analytics with PCI redaction</li>
    <li>All-in-one management tool for accessing recordings, reviews, and notifications</li>
  </ul>

  <p class="copy" style="top:680px">Whether your QA needs revolve around calls, emails, texts, chats or otherwise, VoxGrade's algorithmic and data driven approach allows for a highly dynamic and customizable platform, while maintaining a manageable and user friendly UI for quick adoption and integrated coaching facilitation.</p>

  <p class="copy" style="top:749px">Actively monitoring QA in a variety of verticals including education, mortgage, insurance, transportation, and e-commerce, VoxGrade has decades of combined experience in quality assurance and industry best practices.</p>

  <h2 class="sub-title">BENEFITS OF OUTSOURCING QA</h2>
  <ol class="benefits">
    <li><span>1.</span>Capital Equipment Savings</li>
    <li><span>2.</span>Technology Obsolescence Savings</li>
    <li><span>3.</span>Labor Savings</li>
    <li><span>4.</span>Less Pressure and Stress</li>
    <li><span>5.</span>Improved Morale</li>
    <li><span>6.</span>Scalable Efficiences</li>
    <li><span>7.</span>Unbiased Results</li>
  </ol>
</main>

<footer class="site-footer">
  <div class="f-head" style="left:84px">MENU</div>
  <ul class="f-list" style="left:84px">
    <li>Home</li><li>Who We Are</li><li>Services</li><li>Blog</li><li>Login</li>
  </ul>

  <div class="f-head" style="left:194px">CONTACT US</div>
  <div class="f-line" style="left:194px;top:57px;line-height:10px">4410 Harbor Vale Rd<br>Linden Park, CA 90210</div>
  <div class="f-line" style="left:194px;top:88px">hello@voxgrade.com</div>
  <div class="f-line" style="left:194px;top:107px">800.555.0142</div>

  <div class="f-head" style="left:348px">NEWSLETTER</div>
  <div class="email-field">E MAIL ID</div>
  <div class="signup">SIGNUP</div>

  <div class="f-brand"><span class="brand-dot"></span><span class="brand-name">VoxGrade</span></div>

  <div class="f-rule"></div>

  <div class="follow">FOLLOW US</div>
  <span class="social" style="left:141px;background:#2d5a9a"></span>
  <span class="social" style="left:163px;background:var(--sky)"></span>
  <span class="social" style="left:187px;background:#4d7fa0"></span>
  <span class="social" style="left:211px;background:#e8572c"></span>
  <span class="social" style="left:237px;background:#1c6fb3"></span>

  <div class="copyright">© 2017 VOXGRADE. ALL RIGHTS RESERVED.</div>
</footer>

</body>
</html>
```